Card design for orthopaedic surgeons working as The Brightwater Joint Centre

Business cards, letterhead

Colors

Designer to choose colors to be used in the design.

Requirements
Must have
• Late addition.
• Cards letterhead must have logos of
• Crestmoor Lindell College of Surgeons
• Varenwood Bone Health Association
Nice to have
• Back of card to have space for appointment time to be added by hand and some blank space for writing incidental other notes.

```html
<!DOCTYPE html>
<html lang="en">
<head>
<meta charset="utf-8">
<title>The Brightwater Joint Centre – Letterhead</title>
<link rel="stylesheet" href="https://fonts.googleapis.com/css2?family=Montserrat:wght@400;500;600&display=swap">
<style>
  :root {
    --backdrop: #0e2a45;
    --navy: #0b2440;
    --blue: #1f9bea;
    --ink: #1c3557;
    --muted: #6b7789;
    --paper: #ffffff;
    --paper-shade: #f1f3f6;
    --faint: #e3e6eb;
    --crest: #b9a27a;
  }
  * { box-sizing: border-box; margin: 0; padding: 0; }
  html, body { width: 1200px; height: 837px; overflow: hidden; }
  body {
    background: var(--backdrop);
    font-family: "Montserrat", sans-serif;
    color: var(--ink);
    position: relative;
  }
  .letterhead {
    position: absolute;
    left: 324px; top: 28px;
    width: 552px; height: 780px;
    background: linear-gradient(160deg, var(--paper-shade) 0%, var(--paper) 45%, var(--paper) 80%, var(--paper-shade) 100%);
    overflow: hidden;
  }
  .header-waves, .footer-waves { position: absolute; left: 0; width: 552px; }
  .header-waves { top: 0; height: 170px; }
  .footer-waves { bottom: 0; height: 80px; }
  .header-waves .band-navy, .footer-waves .band-navy { fill: var(--navy); }
  .header-waves .band-blue, .footer-waves .band-blue { fill: var(--blue); }

  .association {
    position: absolute; left: 28px; top: 150px;
    width: 100px; display: flex; flex-direction: column; align-items: center; gap: 5px;
  }
  .association-badge {
    width: 34px; height: 34px; border-radius: 50%; background: var(--crest);
  }
  .association-name {
    font-size: 6.5px; line-height: 1.35; text-align: center; color: var(--muted);
    text-transform: uppercase; letter-spacing: 0.3px; font-weight: 500;
  }
  .centre-name {
    position: absolute; left: 140px; top: 160px;
    font-size: 23px; font-weight: 400; color: var(--ink); letter-spacing: -0.3px;
  }
  .college {
    position: absolute; right: 24px; top: 36px;
    width: 80px; display: flex; flex-direction: column; align-items: center; gap: 4px;
  }
  .college-badge {
    width: 40px; height: 44px; border-radius: 6px; background: var(--crest);
  }
  .college-name {
    font-size: 5.5px; line-height: 1.3; text-align: center; color: var(--muted);
    text-transform: uppercase; font-weight: 500;
  }
  .field {
    position: absolute; display: flex; align-items: flex-end; gap: 6px;
    font-size: 10px; font-weight: 500; color: var(--ink);
  }
  .field-line { display: block; width: 90px; border-bottom: 0.8px solid var(--ink); height: 1px; }
  .field.date { right: 24px; top: 118px; }
  .field.serial { left: 40px; top: 240px; }

  .watermark {
    position: absolute; left: 0; right: 0; top: 430px;
    text-align: center; font-size: 30px; font-weight: 400; color: var(--faint);
  }

  .contact {
    position: absolute; right: 28px; top: 636px;
    list-style: none; display: flex; flex-direction: column; gap: 6px; align-items: flex-end;
  }
  .contact li {
    display: flex; align-items: center; gap: 7px;
    font-size: 8.5px; font-weight: 600; color: var(--ink);
  }
  .contact-icon { width: 13px; height: 13px; }
  .contact-icon circle { fill: var(--navy); }
  .contact-icon path { fill: none; stroke: #fff; stroke-width: 1; stroke-linecap: round; stroke-linejoin: round; }
  .contact-icon .solid { fill: #fff; stroke: none; }
</style>
</head>
<body>
  <main class="letterhead">
    <svg class="header-waves" viewBox="0 0 552 170" aria-hidden="true">
      <path class="band-blue" d="M0 0 H552 V26 C440 40 330 70 230 104 C140 132 60 134 0 150 Z"/>
      <path class="band-navy" d="M0 0 H552 V12 C440 24 330 52 230 84 C140 110 60 112 0 130 Z"/>
    </svg>

    <div class="association">
      <span class="association-badge" role="img" aria-label="Varenwood Bone Health Association badge"></span>
      <span class="association-name">Varenwood Bone<br>Health Association</span>
    </div>

    <h1 class="centre-name">The Brightwater Joint Centre</h1>

    <div class="college">
      <span class="college-badge" role="img" aria-label="Crestmoor Lindell College of Surgeons badge"></span>
      <span class="college-name">Crestmoor Lindell College of Surgeons</span>
    </div>

    <div class="field date">Date <span class="field-line"></span></div>
    <div class="field serial">Sr. # <span class="field-line"></span></div>

    <div class="watermark" aria-hidden="true">The Brightwater Joint Centre</div>

    <ul class="contact">
      <li>+61 2 5550 1842
        <svg class="contact-icon" viewBox="0 0 13 13" aria-hidden="true"><circle cx="6.5" cy="6.5" r="6.5"/><path d="M4.6 3.6h3.8v5.8H4.6z M6 8.4h1"/></svg>
      </li>
      <li>hello@brightwaterjoint.com
        <svg class="contact-icon" viewBox="0 0 13 13" aria-hidden="true"><circle cx="6.5" cy="6.5" r="6.5"/><path d="M3.6 4.6h5.8v4H3.6z M3.6 4.6l2.9 2.1 2.9-2.1"/></svg>
      </li>
      <li>218 Harbour Lane, AU
        <svg class="contact-icon" viewBox="0 0 13 13" aria-hidden="true"><circle cx="6.5" cy="6.5" r="6.5"/><path class="solid" d="M6.5 3.2a2.2 2.2 0 0 1 2.2 2.2c0 1.6-2.2 4.2-2.2 4.2S4.3 7 4.3 5.4a2.2 2.2 0 0 1 2.2-2.2z"/></svg>
      </li>
    </ul>

    <svg class="footer-waves" viewBox="0 0 552 80" aria-hidden="true">
      <path class="band-blue" d="M0 66 C150 40 330 20 552 18 V22 C330 26 150 46 0 72 Z"/>
      <path class="band-navy" d="M0 76 C150 52 330 34 552 30 V80 H0 Z"/>
    </svg>
  </main>
</body>
</html>
```